Business card for medical clinic

I need an upmarket, modern medical/health business card for my clinic

Contact Information for Business Card

name, address, email, qr code

```html
<!DOCTYPE html>
<html lang="en">
<head>
<meta charset="utf-8">
<title>Meridian Care Partners – Business Card</title>
<link rel="stylesheet" href="https://fonts.googleapis.com/css2?family=Poppins:wght@300;400;600&display=swap">
<style>
  :root {
    --stage: #262626;
    --card-white: #ffffff;
    --brand-blue: #29a3dc;
    --brand-blue-deep: #1f8ec4;
    --ink: #1a1a1a;
    --ornament: #ebebf0;
  }
  * { margin: 0; padding: 0; box-sizing: border-box; }
  html, body { width: 1200px; height: 780px; overflow: hidden; }
  body {
    background: var(--stage);
    font-family: "Poppins", sans-serif;
    position: relative;
  }
  .card {
    position: absolute;
    top: 235px;
    width: 540px;
    height: 309px;
    overflow: hidden;
    box-shadow: 0 10px 24px rgba(0,0,0,0.45);
  }
  .card--front { left: 40px; background: var(--card-white); }
  .card--back { left: 620px; background: var(--brand-blue); }

  .ornament-area {
    position: absolute;
    left: 40px;
    top: 130px;
    width: 380px;
    height: 179px;
    background: radial-gradient(ellipse at 60% 100%, var(--ornament) 0%, rgba(235,235,240,0.5) 45%, rgba(255,255,255,0) 75%);
  }

  .brand {
    position: absolute;
    top: 40px;
    right: 36px;
    display: flex;
    align-items: center;
    gap: 10px;
  }
  .brand__dot {
    width: 26px; height: 26px;
    border-radius: 50%;
    background: var(--brand-blue-deep);
  }
  .brand__name {
    font-weight: 600;
    font-size: 17px;
    letter-spacing: 0.06em;
    text-transform: uppercase;
    color: var(--brand-blue-deep);
  }

  .address {
    position: absolute;
    top: 110px;
    right: 56px;
    text-align: right;
    font-weight: 300;
    font-size: 14px;
    line-height: 1.35;
    color: var(--brand-blue);
  }

  .contact {
    position: absolute;
    top: 168px;
    right: 22px;
    list-style: none;
  }
  .contact__item {
    display: flex;
    justify-content: flex-end;
    align-items: center;
    gap: 10px;
    font-weight: 400;
    font-size: 14px;
    line-height: 1;
    color: var(--ink);
    height: 23px;
  }
  .contact__icon { width: 14px; height: 14px; flex: none; }

  .person {
    position: absolute;
    left: 34px;
    bottom: 26px;
  }
  .person__name {
    font-size: 34px;
    line-height: 1;
    color: var(--brand-blue);
  }
  .person__first { font-weight: 600; }
  .person__last { font-weight: 300; }
  .person__title {
    margin-top: 5px;
    font-size: 15px;
    font-weight: 400;
    color: var(--ink);
  }
  .accent-bar {
    position: absolute;
    left: 0;
    bottom: 18px;
    width: 20px;
    height: 60px;
    background: var(--brand-blue);
  }

  .back-pattern {
    position: absolute;
    inset: 0;
    background: linear-gradient(135deg, #2fa9e0 0%, var(--brand-blue) 55%, #2398cf 100%);
  }
  .back-brand {
    position: absolute;
    top: 176px;
    right: 60px;
    display: flex;
    align-items: center;
    gap: 6px;
  }
  .back-brand__dot {
    width: 14px; height: 14px;
    border-radius: 50%;
    border: 1.5px solid #ffffff;
  }
  .back-brand__name {
    font-weight: 600;
    font-size: 9px;
    letter-spacing: 0.06em;
    text-transform: uppercase;
    color: #ffffff;
  }
</style>
</head>
<body>

  <section class="card card--front" aria-label="Business card front">
    <div class="ornament-area" role="img" aria-label="Faint grey decorative sweep behind the name"></div>

    <div class="brand">
      <span class="brand__dot"></span>
      <span class="brand__name">Meridian Care Partners</span>
    </div>

    <p class="address">480 Linden Ave. Suite 310<br>Cedar Falls, TX 75010</p>

    <ul class="contact">
      <li class="contact__item">(555) 214-0387
        <svg class="contact__icon" viewBox="0 0 16 16" aria-hidden="true"><circle cx="8" cy="8" r="8" fill="var(--brand-blue)"/><path d="M5 4.5l1.6-.3.8 2-1 .8a5 5 0 0 0 2.6 2.6l.8-1 2 .8-.3 1.6c-3.4.3-6.8-3.1-6.5-6.5z" fill="#fff"/></svg>
      </li>
      <li class="contact__item">info@meridiancare.com
        <svg class="contact__icon" viewBox="0 0 16 16" aria-hidden="true"><circle cx="8" cy="8" r="8" fill="var(--brand-blue)"/><rect x="4" y="5" width="8" height="6" rx="0.8" fill="#fff"/><path d="M4.3 5.4L8 8.3l3.7-2.9" fill="none" stroke="var(--brand-blue)" stroke-width="0.9"/></svg>
      </li>
      <li class="contact__item">www.meridiancare.com
        <svg class="contact__icon" viewBox="0 0 16 16" aria-hidden="true"><circle cx="8" cy="8" r="8" fill="var(--brand-blue)"/><circle cx="8" cy="8" r="4.2" fill="none" stroke="#fff" stroke-width="1"/><ellipse cx="8" cy="8" rx="1.8" ry="4.2" fill="none" stroke="#fff" stroke-width="0.9"/><path d="M3.8 8h8.4" stroke="#fff" stroke-width="0.9"/></svg>
      </li>
    </ul>

    <span class="accent-bar"></span>
    <div class="person">
      <p class="person__name"><span class="person__first">Nora</span> <span class="person__last">Valen</span></p>
      <p class="person__title">Founder &amp; CEO</p>
    </div>
  </section>

  <section class="card card--back" aria-label="Business card back">
    <div class="back-pattern" role="img" aria-label="Repeating embossed brand pattern on blue"></div>
    <div class="back-brand">
      <span class="back-brand__dot"></span>
      <span class="back-brand__name">Meridian Care Partners</span>
    </div>
  </section>

</body>
</html>
```